Residential real estate home builder in west texas

We need a website design for our home building business based in west Texas called Birch Hollow homes. We build new construction for potential homeowners in Amarillo. Currently we do not have any completed construction, but we have floor plans and architectural drawings of the front elevation. The website would need to be able to properly advertise a architectural drawing, floor plans, and descriptive content at the initial phase. The website will need to be simple but professional with generic picture content.
The website will need the ability to be updated in the future for the additions of home pictures, and video content and virtual tours of the homes.

Target Market(s)

Potential Home buyers

Industry/Entity Type

Real Estate

Number of Pages Required

5+ page

Font styles to use
Sans Serif

Colors
f37122
757575

Requirements
Must have
• Web design must be simple and easy to navigate. There is not much picture content, so it will need to be simple.
• 5 pages:
• Home, Available homes, Available floor plans, guide to ownership, Contact
• The website will need the ability to be updated in the future for the additions of pictures, and video content of the homes when they are built. ( A virtual tour).
Nice to have
• I would like to see a modern and cohesive design. Contact information at the bottom of each page.
Should not have
• A Black background

```html
<!DOCTYPE html>
<html lang="en">
<head>
<meta charset="utf-8">
<title>Birch Hollow Homes</title>
<link href="https://fonts.googleapis.com/css2?family=Montserrat:wght@400;500;600;700&family=Open+Sans:ital,wght@0,400;0,600;1,400&display=swap" rel="stylesheet">
<style>
:root{
  --orange:#f37122;
  --orange-dark:#e05a1a;
  --grey:#757575;
  --ink:#2b2b2b;
  --light:#f4f4f4;
  --line:#e2e2e2;
  --white:#ffffff;
}
*{margin:0;padding:0;box-sizing:border-box}
html,body{width:1200px;height:3249px;overflow:hidden}
body{position:relative;background:var(--white);font-family:"Open Sans",Arial,sans-serif;color:var(--grey)}
.abs{position:absolute}
.btn{position:absolute;background:var(--orange);color:var(--white);font-family:"Montserrat",Arial,sans-serif;font-size:12px;font-weight:600;letter-spacing:.5px;text-transform:uppercase;display:flex;align-items:center;justify-content:center}
.section-title{position:absolute;left:0;width:1200px;text-align:center;font-family:"Montserrat",Arial,sans-serif;font-weight:500;font-size:26px;color:var(--ink);text-transform:uppercase}

/* header */
.brand{left:130px;top:28px;font-family:"Montserrat",Arial,sans-serif;font-weight:600;font-size:26px;color:var(--orange);display:flex;align-items:center;gap:10px;text-transform:uppercase;letter-spacing:1px}
.brand-mark{width:14px;height:14px;background:var(--orange);flex:none}
.foot-brand{left:132px;top:3012px;width:220px;font-size:22px;line-height:28px;letter-spacing:1px}
.foot-brand .name{width:190px;text-align:center}
.call{left:748px;top:16px;font-size:17px;color:var(--grey);display:flex;align-items:center;gap:8px}
.social{left:960px;top:16px;display:flex;gap:5px}
.social span{width:22px;height:22px;border:1.5px solid var(--orange);border-radius:50%}
.nav{left:455px;top:78px;width:615px;display:flex;justify-content:space-between;font-size:11.5px;color:var(--ink);text-transform:uppercase}
.nav a{color:inherit;text-decoration:none;padding:0 12px;border-left:1px solid var(--line)}
.nav a:first-child{border-left:none;color:var(--orange);padding-left:0}
.nav a:last-child{padding-right:0}

/* hero */
.hero{left:0;top:108px;width:1200px;height:600px;background:linear-gradient(180deg,#6f82c6 0%,#a6b2dc 30%,#c9b7a0 55%,#6f6458 80%,#3e4a32 100%)}
.hero-title{left:0;top:292px;width:1200px;text-align:center;color:var(--white);font-family:"Montserrat",Arial,sans-serif;font-weight:600;font-size:46px;text-transform:uppercase}
.hero-sub{left:0;top:357px;width:1200px;text-align:center;color:var(--white);font-size:17px}
.dots{left:560px;top:640px;display:flex;gap:16px}
.dots span{width:16px;height:16px;border-radius:50%;border:2px solid var(--white)}
.dots span:first-child{background:var(--orange);border-color:var(--orange)}

/* welcome */
.intro{left:200px;top:785px;width:800px;text-align:center;font-size:13px;line-height:22px}
.feature{position:absolute;top:857px;width:200px;text-align:center}
.feature .icon{width:88px;height:88px;border-radius:50%;background:var(--grey);margin:0 auto;display:flex;align-items:center;justify-content:center}
.feature.active .icon{background:var(--orange)}
.feature h4{margin-top:20px;font-size:12.5px;font-weight:400;color:var(--ink);text-transform:uppercase}
.feature.active h4{color:var(--orange)}
.feature p{margin-top:8px;font-size:11.5px;line-height:20px}

/* services */
.services{left:0;top:1092px;width:1200px;height:601px;background:var(--light)}
.tile{position:absolute;width:469px;height:206px}
.tile-text{background:var(--white);text-align:center;padding:34px 50px 0}
.tile-text h3{font-family:"Montserrat",Arial,sans-serif;font-size:14px;font-weight:600;color:var(--ink);text-transform:uppercase}
.tile-text p{margin-top:12px;font-size:11.5px;line-height:20px}
.tile-text .btn{left:185px;width:98px;height:34px;bottom:34px}
.photo-desk{background:linear-gradient(135deg,#8a6b4a,#d8dde2 45%,#b0bcc8 70%,#6b5138)}
.photo-plan{background:linear-gradient(135deg,#e8eef6,#9cb2cf 55%,#3d5e8c)}

/* tours */
.tours{left:0;top:1693px;width:1200px;height:412px;background:linear-gradient(180deg,#22303f 0%,#1c2a38 60%,#2e3a33 100%)}
.tours-title{left:130px;top:1752px;color:var(--white);font-family:"Montserrat",Arial,sans-serif;font-weight:500;font-size:26px}
.tours-text{position:absolute;left:130px;width:470px;color:#e6e6e6;font-size:11.5px;line-height:20px}
.video{left:631px;top:1762px;width:437px;height:271px;border:5px solid var(--white);background:var(--white)}
.video-frame{width:100%;height:233px;background:linear-gradient(180deg,#5b8fd6 0%,#a9c8ee 40%,#b7a89a 62%,#5f9a3c 80%,#4c8a2c 100%);position:relative}
.video-bar{height:28px;display:flex;align-items:center;gap:10px;padding:0 8px;font-size:9px;color:var(--ink)}
.track{flex:1;height:4px;background:#ccc;position:relative}
.track i{position:absolute;left:0;top:0;width:55%;height:4px;background:var(--orange)}

/* testimonials */
.quote{position:absolute;top:2215px;width:442px;height:150px;border:1px solid var(--line);background:var(--white);padding:22px 26px 0 52px;font-size:13px;font-style:italic;line-height:22px;color:var(--grey)}
.quote::before{content:"\201C";position:absolute;left:24px;top:12px;font-size:36px;font-style:normal;color:var(--grey)}
.quote::after{content:"\201D";position:absolute;right:24px;bottom:-4px;font-size:60px;font-style:normal;color:#d5d5d5}
.avatar{position:absolute;top:2330px;width:62px;height:62px;border-radius:50%;background:linear-gradient(180deg,#b9b1a6,#6d6257);border:3px solid var(--white)}
.person{position:absolute;top:2343px}
.person b{display:block;color:var(--orange);font-size:13px;font-weight:600;text-transform:uppercase}
.person span{font-size:10px;font-style:italic}

/* projects */
.projects{left:0;top:2460px;width:1200px;height:465px;background:var(--orange-dark)}
.project{position:absolute;top:2627px;width:234px;height:224px;background:var(--white)}
.project .shot{height:185px}
.project .cap{height:39px;display:flex;align-items:center;justify-content:center;gap:6px;font-size:12px;color:var(--ink);text-transform:uppercase;border-left:1px solid var(--line)}

/* footer */
.footer{left:0;top:2925px;width:1200px;height:270px;background:#f2f2f2}
.foot-h{position:absolute;top:2963px;font-family:"Montserrat",Arial,sans-serif;font-size:14px;color:var(--ink);text-transform:uppercase}
.foot-row{position:absolute;left:390px;width:270px;display:flex;align-items:flex-start;gap:14px;font-size:11px;line-height:20px;color:var(--grey)}
.foot-row svg{flex:none;margin-top:3px}
.field{position:absolute;width:225px;height:40px;background:var(--white);font-size:11px;color:var(--ink);padding:12px 10px}
.links{left:961px;top:2995px;font-size:11.5px;line-height:26px;color:var(--ink);list-style:none}
.copy{left:0;top:3195px;width:1200px;height:54px;display:flex;align-items:center;justify-content:center;font-size:11px;color:var(--ink)}
</style>
</head>
<body>

<!-- header -->
<div class="abs brand"><span class="brand-mark"></span>Birch Hollow Homes</div>
<div class="abs call">
  <svg width="20" height="20" viewBox="0 0 20 20"><circle cx="10" cy="10" r="9" fill="none" stroke="#f37122" stroke-width="1.6"/><path d="M7 5.5l1.6 2.2-1 1.2c.6 1.3 1.6 2.3 2.9 2.9l1.2-1 2.2 1.6-.8 1.8c-3.6-.3-6.6-3.3-6.9-6.9z" fill="#f37122"/></svg>
  Call Us 888-555-0142
</div>
<div class="abs social"><span></span><span></span><span></span><span></span></div>
<svg class="abs" style="left:455px;top:50px" width="615" height="24" viewBox="0 0 615 24">
  <path d="M0 20 L18 5 L36 20" fill="none" stroke="#f37122" stroke-width="2.5"/>
  <line x1="36" y1="20" x2="615" y2="20" stroke="#f37122" stroke-width="2.5"/>
</svg>
<nav class="abs nav">
  <a>Home</a><a>Available Homes</a><a>Available Floor Plans</a><a>Guide to Ownership</a><a>Contact</a>
</nav>

<!-- hero -->
<div class="abs hero" role="img" aria-label="Photo of a two-storey suburban house with a garage at dusk"></div>
<div class="abs hero-title">Birch Hollow Homes</div>
<div class="abs hero-sub">Excepteur sint occaecat cupidatat</div>
<div class="btn" style="left:520px;top:402px;width:160px;height:46px">Learn More Info</div>
<svg class="abs" style="left:0;top:540px" width="1200" height="170" viewBox="0 0 1200 170">
  <polygon points="0,14 600,168 1200,14 1200,170 0,170" fill="#ffffff"/>
  <polygon points="0,0 600,130 1200,0 1200,14 600,168 0,14" fill="#f37122"/>
  <polygon points="0,30 600,168 0,45" fill="#f37122" opacity=".6"/>
</svg>
<div class="abs dots"><span></span><span></span><span></span></div>

<!-- welcome -->
<h2 class="section-title" style="top:742px">Welcome to Birch Hollow Homes</h2>
<p class="abs intro">Lorem ipsum dolor sit amet, consectetur adipiscing elit, sed do eiusmod tempor incididunt ut labore et dolore magna aliqua. Ut enim ad minim veniam, quis nostrud exercitation ullamco laboris nisi ut aliquip ex ea commodo consequat...</p>

<div class="feature active" style="left:132px">
  <div class="icon"><svg width="44" height="44" viewBox="0 0 44 44" fill="none" stroke="#fff" stroke-width="2.5"><path d="M6 22 L22 8 L38 22"/><path d="M11 18 V37 H33 V18"/><rect x="18" y="26" width="8" height="11"/></svg></div>
  <h4>Tempor Incididunt</h4>
  <p>Lorem ipsum dolor sit amet, consectetur adipiscing elit, sed do eiusmod tempor incididunt ut labore...</p>
</div>
<div class="feature" style="left:375px">
  <div class="icon"><svg width="44" height="44" viewBox="0 0 44 44" fill="none" stroke="#fff" stroke-width="2.5"><path d="M8 36 L36 36 L8 8 Z"/><path d="M14 30 L22 30 L14 22 Z"/><line x1="26" y1="8" x2="36" y2="18"/></svg></div>
  <h4>Tempor Incididunt</h4>
  <p>Lorem ipsum dolor sit amet, consectetur adipiscing elit, sed do eiusmod tempor incididunt ut labore...</p>
</div>
<div class="feature" style="left:622px">
  <div class="icon"><svg width="44" height="44" viewBox="0 0 44 44" fill="none" stroke="#fff" stroke-width="2.5"><rect x="8" y="8" width="28" height="28"/><line x1="8" y1="20" x2="24" y2="20"/><line x1="24" y1="8" x2="24" y2="28"/><line x1="16" y1="28" x2="36" y2="28"/></svg></div>
  <h4>Tempor Incididunt</h4>
  <p>Lorem ipsum dolor sit amet, consectetur adipiscing elit, sed do eiusmod tempor incididunt ut labore...</p>
</div>
<div class="feature" style="left:868px">
  <div class="icon"><svg width="44" height="44" viewBox="0 0 44 44" fill="none" stroke="#fff" stroke-width="2.5"><circle cx="17" cy="19" r="7"/><circle cx="17" cy="19" r="2.5"/><circle cx="30" cy="30" r="5"/><path d="M17 9v3M17 26v3M7 19h3M24 19h3M10 12l2 2M22 24l2 2M24 12l-2 2M10 26l2-2"/></svg></div>
  <h4>Tempor Incididunt</h4>
  <p>Lorem ipsum dolor sit amet, consectetur adipiscing elit, sed do eiusmod tempor incididunt ut labore...</p>
</div>

<!-- services -->
<div class="abs services"></div>
<h2 class="section-title" style="top:1152px">What We Do?</h2>
<div class="tile photo-desk" style="left:132px;top:1211px" role="img" aria-label="Photo of a person sketching house plans at a desk"></div>
<div class="tile tile-text" style="left:601px;top:1211px">
  <h3>Floor Plans</h3>
  <p>Sed ut perspiciatis unde omnis or sit voluptSed ut perspiciatis unde omnis voluptatem accusantium dorem que laudantium, totam rem ampe loreque laudantium atem accusantium...</p>
  <div class="btn">Read More</div>
</div>
<div class="tile tile-text" style="left:132px;top:1417px">
  <h3>Architectural Drawings</h3>
  <p>Sed ut perspiciatis unde omnis or sit voluptSed ut perspiciatis unde omnis voluptatem accusantium dorem que laudantium, totam rem ampe loreque laudantium atem accusantium...</p>
  <div class="btn">Read More</div>
</div>
<div class="tile photo-plan" style="left:601px;top:1417px" role="img" aria-label="Photo of rolled blueprints and a pen"></div>
<svg class="abs" style="left:823px;top:1417px" width="24" height="12" viewBox="0 0 24 12"><polygon points="0,0 24,0 12,12" fill="#fff"/></svg>
<svg class="abs" style="left:354px;top:1405px" width="24" height="12" viewBox="0 0 24 12"><polygon points="0,12 24,12 12,0" fill="#fff"/></svg>

<!-- tours -->
<div class="abs tours" role="img" aria-label="Dimmed photo of a house at night"></div>
<h2 class="abs tours-title">VIRTUAL TOURS</h2>
<p class="tours-text" style="top:1797px">Sed ut perspiciatis unde omnis iste natus error sit voluptatem accusan doloremque laudantium, totam rem aperiam, eaque ipsa quae ab illo inventore veritatis et quasi architecto beatae vitae dicta sunt explicabo. Nemo enim ipsam voluptatem quia voluptas sit aspernatur aut odit aut fugit, sed quia consequuntur...</p>
<p class="tours-text" style="top:1895px">Sed ut perspiciatis unde omnis iste natus error sit voluptatem accusantium doloremque laudantium, totam rem aperiam, eaque ipsa quae ab illo inventore veritatis et quasi architecto beatae vitae dicta sunt explicabo.</p>
<div class="btn" style="left:130px;top:1992px;width:128px;height:42px;gap:6px">More Videos
  <svg width="12" height="12" viewBox="0 0 12 12"><circle cx="6" cy="6" r="5.5" fill="#fff"/><path d="M5 3.5L7.5 6 5 8.5" stroke="#f37122" stroke-width="1.5" fill="none"/></svg></div>
<div class="abs video">
  <div class="video-frame" role="img" aria-label="Video still of a suburban house with a green lawn">
    <svg style="position:absolute;left:186px;top:84px" width="56" height="56" viewBox="0 0 56 56"><circle cx="28" cy="28" r="26" fill="rgba(0,0,0,.55)" stroke="#fff" stroke-width="2"/><polygon points="22,17 40,28 22,39" fill="#fff"/></svg>
  </div>
  <div class="video-bar">
    <svg width="10" height="10" viewBox="0 0 10 10"><polygon points="1,0 10,5 1,10" fill="#2b2b2b"/></svg>
    <span>00:00:00</span>
    <div class="track"><i></i></div>
    <svg width="12" height="10" viewBox="0 0 12 10"><polygon points="0,3 3,3 7,0 7,10 3,7 0,7" fill="#2b2b2b"/></svg>
    <div style="width:40px;height:4px;background:#f37122"></div>
  </div>
</div>

<!-- testimonials -->
<h2 class="section-title" style="top:2155px">Testimonials</h2>
<svg class="abs" style="left:118px;top:2280px" width="14" height="20" viewBox="0 0 14 20"><path d="M11 2L3 10l8 8" stroke="#999" stroke-width="3" fill="none"/></svg>
<svg class="abs" style="left:1066px;top:2280px" width="14" height="20" viewBox="0 0 14 20"><path d="M3 2l8 8-8 8" stroke="#999" stroke-width="3" fill="none"/></svg>
<div class="quote" style="left:150px">Tempor incididunt ut labore et dolore magna aliqua. Ut enim ad minim veniam, quis nostrud exercitation ullamco laboris nisi ut aliquip ex ea commodo consequat...</div>
<div class="quote" style="left:610px">Tempor incididunt ut labore et dolore magna aliqua. Ut enim ad minim veniam, quis nostrud exercitation ullamco laboris nisi ut aliquip ex ea commodo consequat...</div>
<div class="avatar" style="left:190px" role="img" aria-label="Portrait of a client"></div>
<div class="person" style="left:270px"><b>Dana Reyes</b><span>Excepteur sint occaecat</span></div>
<div class="avatar" style="left:650px" role="img" aria-label="Portrait of a client"></div>
<div class="person" style="left:730px"><b>Dana Reyes</b><span>Excepteur sint occaecat</span></div>

<!-- projects -->
<div class="abs projects"></div>
<h2 class="section-title" style="top:2522px;color:#fff">Recent Projects</h2>
<p class="abs" style="left:240px;top:2562px;width:720px;text-align:center;color:#fff;font-size:11.5px;line-height:20px">Excepteur sint occaecat cupidatat non proident, sunt in culpa qui officia deserunt mollit anim id est laborum ullamco laboris nisi ut aliquip ex ea commodo consequat...</p>
<div class="project" style="left:134px"><div class="shot" role="img" aria-label="Photo of a grey family home with driveway" style="background:linear-gradient(180deg,#cfd8e0,#a9a59c 60%,#7d8a5c)"></div><div class="cap">Consectet Adipiscing <svg width="11" height="11" viewBox="0 0 12 12"><circle cx="6" cy="6" r="5.5" fill="#2b2b2b"/><path d="M5 3.5L7.5 6 5 8.5" stroke="#fff" stroke-width="1.5" fill="none"/></svg></div></div>
<div class="project" style="left:368px"><div class="shot" role="img" aria-label="Photo of a modern white house with a pool at dusk" style="background:linear-gradient(180deg,#3e5f9e,#c7cfe0 45%,#d08a4a 75%,#6aa8c8)"></div><div class="cap">Consectet Adipiscing <svg width="11" height="11" viewBox="0 0 12 12"><circle cx="6" cy="6" r="5.5" fill="#2b2b2b"/><path d="M5 3.5L7.5 6 5 8.5" stroke="#fff" stroke-width="1.5" fill="none"/></svg></div></div>
<div class="project" style="left:602px"><div class="shot" role="img" aria-label="Photo of a contemporary wood and glass house on a lawn" style="background:linear-gradient(180deg,#8fb4dc,#6b5a4a 50%,#5e9a3a)"></div><div class="cap">Consectet Adipiscing <svg width="11" height="11" viewBox="0 0 12 12"><circle cx="6" cy="6" r="5.5" fill="#2b2b2b"/><path d="M5 3.5L7.5 6 5 8.5" stroke="#fff" stroke-width="1.5" fill="none"/></svg></div></div>
<div class="project" style="left:836px"><div class="shot" role="img" aria-label="Photo of a brick house with a wide green lawn" style="background:linear-gradient(180deg,#7faee6,#c2dcf2 35%,#a9603e 60%,#5aa03a)"></div><div class="cap">Consectet Adipiscing <svg width="11" height="11" viewBox="0 0 12 12"><circle cx="6" cy="6" r="5.5" fill="#2b2b2b"/><path d="M5 3.5L7.5 6 5 8.5" stroke="#fff" stroke-width="1.5" fill="none"/></svg></div></div>

<!-- footer -->
<div class="abs footer"></div>
<div class="abs brand foot-brand"><span class="brand-mark"></span><span class="name">Birch Hollow<br>Homes</span></div>

<div class="foot-h" style="left:390px">Contact Us</div>
<div class="foot-row" style="top:2998px">
  <svg width="12" height="16" viewBox="0 0 12 16"><path d="M6 0a6 6 0 0 1 6 6c0 4-6 10-6 10S0 10 0 6a6 6 0 0 1 6-6z" fill="#f37122"/><circle cx="6" cy="6" r="2" fill="#fff"/></svg>
  <span>Birch Hollow homes P.O. Box 1200,<br>Canyon Road, Amarillo-791</span>
</div>
<div class="foot-row" style="top:3058px">
  <svg width="14" height="14" viewBox="0 0 14 14"><path d="M2 1l3 3-1.5 2c1 2 2.5 3.5 4.5 4.5L10 9l3 3-2 2C5 14 0 9 0 3z" fill="#f37122"/></svg>
  <span>Phone: 888-555-0142</span>
</div>
<div class="foot-row" style="top:3102px">
  <svg width="14" height="12" viewBox="0 0 14 12"><rect width="14" height="12" fill="#f37122"/><path d="M0 0l7 6 7-6" stroke="#fff" stroke-width="1.3" fill="none"/></svg>
  <span>Email: info@birchhollowhomes.com</span>
</div>

<div class="foot-h" style="left:681px">Sign Up for Newsletter</div>
<p class="abs" style="left:681px;top:2993px;width:230px;font-size:11px;line-height:19px;color:var(--ink)">Get the latest updates on our courses and events: Notify Me</p>
<div class="field" style="left:681px;top:3040px">Enter Name</div>
<div class="field" style="left:681px;top:3084px;width:128px">Enter Email</div>
<div class="btn" style="left:811px;top:3084px;width:95px;height:40px">Subscribe</div>

<div class="foot-h" style="left:961px">Quick Links</div>
<ul class="abs links">
  <li>Home</li><li>Available Homes</li><li>Available Floor Plans</li><li>Guide to Ownership</li><li>Contact</li>
</ul>

<div class="abs copy">©2016 - 2017 Birch Hollow homes. All Rights Reserved.</div>

</body>
</html>
```